Business Card Design

I need a business card for a new company based in Australia called "MedLinkora".

Its a cloud program for GPs that allows them to search for the specialist they require using a simple user friendly tool.

I would like the colours to match those in the program (the colours in the logo attached).

The final design should reflect the programs clarity, ease of use and professionalism.

Target Market(s)

GPs and other Health Professionals

Industry/Entity Type

Business

Contact Information for Business Card

MedLinkora; The Whole Consultant Index; Marla Voss CEO; 0438215967; marla@medlinkora.example; www.medlinkora.example

Requirements
Must have
• Must have the logo attached; the web address and my name and phone number
Nice to have
• the slogan "The Whole Consultant Index"

```html
<!DOCTYPE html>
<html lang="en">
<head>
<meta charset="utf-8">
<title>MedLinkora Business Card</title>
<link href="https://fonts.googleapis.com/css2?family=Questrial&family=Open+Sans:wght@400;600;700&display=swap" rel="stylesheet">
<style>
  :root {
    --brand-blue: #1fb6e6;
    --card-black: #050505;
    --card-white: #ffffff;
    --text-grey: #8a8a8a;
    --swoosh-grey: #9a9a9a;
    --ink-dark: #3a3a3a;
    --page-bg: #ececec;
  }
  * { box-sizing: border-box; margin: 0; padding: 0; }
  html, body { width: 1200px; height: 829px; overflow: hidden; }
  body {
    background: var(--page-bg);
    display: flex;
    align-items: center;
    justify-content: center;
    gap: 40px;
  }
  .card {
    position: relative;
    width: 540px;
    height: 310px;
    overflow: hidden;
    box-shadow: 0 6px 18px rgba(0,0,0,0.18);
  }
  .card--front { background: var(--card-black); }
  .card--back { background: var(--card-white); }

  .brand-name {
    font-family: "Questrial", sans-serif;
    font-weight: 400;
    color: var(--brand-blue);
    line-height: 1;
    letter-spacing: -0.5px;
  }
  .brand-tagline {
    font-family: "Questrial", sans-serif;
    color: var(--text-grey);
    line-height: 1;
    letter-spacing: 0.3px;
  }

  /* front */
  .front-brand { position: absolute; left: 56px; top: 46px; }
  .front-brand .brand-name { font-size: 50px; }
  .front-brand .brand-tagline { font-size: 15px; margin-top: 4px; padding-left: 4px; }

  .front-person {
    position: absolute; left: 88px; top: 160px; text-align: right; width: 150px;
    font-family: "Open Sans", sans-serif;
  }
  .person-name { color: var(--brand-blue); font-weight: 700; font-size: 17px; }
  .person-role { color: var(--text-grey); font-size: 11px; margin-top: 2px; }

  .front-divider {
    position: absolute; left: 256px; top: 122px; width: 1px; height: 78px;
    background: var(--text-grey);
  }
  .contact-list {
    position: absolute; left: 268px; top: 120px; list-style: none;
    font-family: "Open Sans", sans-serif; font-size: 14px; color: #ffffff;
  }
  .contact-item { display: flex; align-items: center; gap: 8px; height: 27px; }
  .contact-icon { width: 15px; height: 15px; flex: none; }

  .front-swoosh { position: absolute; left: 0; top: 0; }

  /* back */
  .back-brand {
    position: absolute; left: 0; right: 0; top: 94px; text-align: center;
  }
  .back-brand .brand-name { font-size: 62px; }
  .back-brand .brand-tagline { font-size: 18px; margin-top: 4px; }
  .back-web {
    position: absolute; left: 0; right: 0; top: 212px; text-align: center;
    font-family: "Open Sans", sans-serif; font-weight: 600; font-size: 19px;
    color: var(--ink-dark); letter-spacing: 1px;
  }
</style>
</head>
<body>

<section class="card card--front" aria-label="Card front">
  <svg class="front-swoosh" width="540" height="310" viewBox="0 0 540 310" aria-hidden="true">
    <path d="M0,272 C150,250 330,262 430,236 C480,223 515,214 540,210 L540,224 C515,228 480,238 430,252 C330,278 150,268 0,286 Z" fill="var(--swoosh-grey)"/>
    <path d="M0,286 C150,268 330,278 430,252 C480,238 515,228 540,224 L540,242 C515,246 490,258 440,272 C340,298 150,292 0,302 Z" fill="var(--brand-blue)"/>
  </svg>

  <div class="front-brand">
    <div class="brand-name">MedLinkora</div>
    <div class="brand-tagline">The Whole Consultant Index</div>
  </div>

  <div class="front-person">
    <div class="person-name">Marla Voss</div>
    <div class="person-role">CEO</div>
  </div>

  <div class="front-divider"></div>

  <ul class="contact-list">
    <li class="contact-item">
      <svg class="contact-icon" viewBox="0 0 16 16" aria-hidden="true">
        <circle cx="8" cy="8" r="8" fill="var(--brand-blue)"/>
        <path d="M5.2,4 L6.8,4 L7.4,6 L6.4,6.8 C6.9,7.9 7.9,8.9 9.1,9.5 L9.9,8.5 L11.9,9.1 L11.9,10.7 C8.1,11 4.9,7.8 5.2,4 Z" fill="#000"/>
      </svg>
      <span>0438215967</span>
    </li>
    <li class="contact-item">
      <svg class="contact-icon" viewBox="0 0 16 16" aria-hidden="true">
        <circle cx="8" cy="8" r="8" fill="var(--brand-blue)"/>
        <rect x="4" y="5.3" width="8" height="5.6" fill="#000"/>
        <path d="M4,5.3 L8,8.6 L12,5.3" fill="none" stroke="var(--brand-blue)" stroke-width="0.9"/>
      </svg>
      <span>marla@medlinkora.example</span>
    </li>
    <li class="contact-item">
      <svg class="contact-icon" viewBox="0 0 16 16" aria-hidden="true">
        <circle cx="8" cy="8" r="8" fill="var(--brand-blue)"/>
        <circle cx="8" cy="8" r="4.2" fill="none" stroke="#000" stroke-width="1"/>
        <ellipse cx="8" cy="8" rx="1.8" ry="4.2" fill="none" stroke="#000" stroke-width="0.9"/>
        <line x1="3.8" y1="8" x2="12.2" y2="8" stroke="#000" stroke-width="0.9"/>
      </svg>
      <span>www.medlinkora.example</span>
    </li>
  </ul>
</section>

<section class="card card--back" aria-label="Card back">
  <div class="back-brand">
    <div class="brand-name">MedLinkora</div>
    <div class="brand-tagline">The Whole Consultant Index</div>
  </div>
  <div class="back-web">www.medlinkora.example</div>
</section>

</body>
</html>
```